1876 Basins & Spouts Business Card

I'm wanting to get a business card designed. Our business is 1876 Basins & Spouts
Details for the card:

1876 Basins & Spouts
Name: Harold Vesk
Email: harold@1876basinsandspouts.com.au
Website: www.1876basinsandspouts.com.au
Mobile: 0438 260 947
Phone: 02 7481 3926

Font of Basins & Spouts is called Snell Roundhand. Not sue what font logo text is.

I'm thinking two sided but it doesn't have to be.

```html
<!DOCTYPE html>
<html lang="en">
<head>
<meta charset="utf-8">
<title>1876 Basins &amp; Spouts — Business Card</title>
<link href="https://fonts.googleapis.com/css2?family=Lato:wght@400;700&display=swap" rel="stylesheet">
<style>
  :root {
    --bg: #6e6e6e;
    --card-white: #ffffff;
    --card-black: #0a0a0b;
    --ink: #111111;
    --ink-soft: #555555;
    --rule: #d4d4d4;
    --wave-grey: #8a8a8a;
    --paper-on-dark: #f2f2f2;
  }
  * { margin: 0; padding: 0; box-sizing: border-box; }
  html, body {
    width: 1200px; height: 1200px; overflow: hidden;
    background: var(--bg);
    font-family: "Lato", Arial, sans-serif;
  }
  .card {
    position: absolute; left: 240px; width: 720px; height: 420px;
    border-radius: 32px; overflow: hidden;
  }
  .card--front { top: 142px; background: var(--card-white); }
  .card--back { top: 638px; background: var(--card-black); }

  .brand {
    position: absolute; display: flex; align-items: center; gap: 12px;
    font-weight: 400; white-space: nowrap;
  }
  .brand__dot { border-radius: 50%; flex: none; }
  .card--front .brand { right: 30px; top: 78px; font-size: 24px; color: var(--ink); }
  .card--front .brand__dot { width: 22px; height: 22px; background: var(--ink); }
  .card--back .brand { left: 50%; top: 188px; transform: translateX(-50%); font-size: 36px; color: var(--paper-on-dark); }
  .card--back .brand__dot { width: 30px; height: 30px; background: var(--paper-on-dark); }

  .holder {
    position: absolute; left: 37px; top: 158px;
    font-size: 26px; font-weight: 700; color: var(--ink);
  }
  .rule-long { position: absolute; left: 37px; right: 30px; top: 211px; height: 1px; background: var(--rule); }
  .rule-short { position: absolute; left: 37px; top: 210px; width: 144px; height: 2px; background: var(--ink-soft); }

  .contacts { position: absolute; left: 37px; top: 228px; list-style: none; }
  .contacts li {
    display: flex; align-items: center; gap: 11px;
    height: 25.5px; font-size: 17.5px; color: var(--ink-soft);
  }
  .contacts svg { width: 14px; height: 14px; fill: var(--ink); flex: none; }

  .address {
    position: absolute; right: 30px; top: 282px; text-align: right;
    font-size: 16.5px; line-height: 21px; color: var(--ink-soft); font-style: normal;
  }
  .wave { position: absolute; left: 0; top: 0; width: 720px; height: 420px; }

  .trade-name {
    position: absolute; left: 0; right: 0; top: 360px; text-align: center;
    font-size: 18px; color: var(--paper-on-dark);
  }
</style>
</head>
<body>

<section class="card card--front">
  <svg class="wave" viewBox="0 0 720 420" aria-hidden="true">
    <path d="M0 374 C150 398 260 402 420 380 C560 360 640 350 720 352 L720 420 L0 420 Z" fill="var(--wave-grey)"/>
    <path d="M0 382 C150 406 260 410 420 388 C560 368 640 358 720 360 L720 420 L0 420 Z" fill="var(--card-black)"/>
    <path d="M0 368 C150 390 260 394 420 372 C560 352 640 342 720 346" fill="none" stroke="var(--card-black)" stroke-width="2"/>
  </svg>

  <div class="brand"><span class="brand__dot"></span>1876 Basins &amp; Spouts</div>

  <h1 class="holder">Harold Vesk</h1>
  <div class="rule-long"></div>
  <div class="rule-short"></div>

  <ul class="contacts">
    <li><svg viewBox="0 0 24 24"><path d="M6.6 10.8a15.1 15.1 0 0 0 6.6 6.6l2.2-2.2a1 1 0 0 1 1-.25 11.4 11.4 0 0 0 3.6.57 1 1 0 0 1 1 1V20a1 1 0 0 1-1 1A17 17 0 0 1 3 4a1 1 0 0 1 1-1h3.5a1 1 0 0 1 1 1c0 1.25.2 2.45.57 3.57a1 1 0 0 1-.25 1z"/></svg>02 7481 3926</li>
    <li><svg viewBox="0 0 24 24"><path d="M7 1h10a2 2 0 0 1 2 2v18a2 2 0 0 1-2 2H7a2 2 0 0 1-2-2V3a2 2 0 0 1 2-2zm0 3v14h10V4zm5 15.5a1.2 1.2 0 1 0 0 2.4 1.2 1.2 0 0 0 0-2.4z"/></svg>0438 260 947</li>
    <li><svg viewBox="0 0 24 24"><path d="M2 5h20v14H2zm2 2v.5l8 5 8-5V7zm0 2.8V17h16V9.8l-8 5z"/></svg>harold@1876basinsandspouts.com.au</li>
    <li><svg viewBox="0 0 24 24"><path d="M12 2a10 10 0 1 0 0 20 10 10 0 0 0 0-20zm6.9 6h-2.9a15 15 0 0 0-1.3-3.6A8 8 0 0 1 18.9 8zM12 4a13 13 0 0 1 1.9 4h-3.8A13 13 0 0 1 12 4zM4.3 14a8 8 0 0 1 0-4h3.4a16 16 0 0 0 0 4zm.8 2h2.9a15 15 0 0 0 1.3 3.6A8 8 0 0 1 5.1 16zM8 8H5.1a8 8 0 0 1 4.2-3.6A15 15 0 0 0 8 8zm4 12a13 13 0 0 1-1.9-4h3.8A13 13 0 0 1 12 20zm2.3-6H9.7a14 14 0 0 1 0-4h4.6a14 14 0 0 1 0 4zm.4 5.6A15 15 0 0 0 16 16h2.9a8 8 0 0 1-4.2 3.6zm1.6-5.6a16 16 0 0 0 0-4h3.4a8 8 0 0 1 0 4z"/></svg>www.1876basinsandspouts.com.au</li>
  </ul>

  <address class="address">Larkfield Crossing<br>Ashmoor Vale, 1642</address>
</section>

<section class="card card--back">
  <div class="brand"><span class="brand__dot"></span>1876 Basins &amp; Spouts</div>
  <p class="trade-name">1876 Basins &amp; Spouts</p>
</section>

</body>
</html>
```